Mental Health Clinic Website

website for a mental health clinic. two files describing the website are attached, in case of conflicting info the word document is priority.

Target Market(s)

Ohio / Pennsylvania residents

Industry/Entity Type

Health Care

Coding

Coded - Design and coding required

Number of Pages Required

5+ page

Requirements
Must have
• see attached

```html
<!DOCTYPE html>
<html lang="en">
<head>
<meta charset="utf-8">
<title>Dr Halvorsen Serenity Center</title>
<link href="https://fonts.googleapis.com/css2?family=Montserrat:wght@400;500;600;700;800&family=Open+Sans:wght@400;600&display=swap" rel="stylesheet">
<style>
:root{
  --green:#4caf3b;
  --green-dark:#3d9a2e;
  --blue:#1f5fb4;
  --blue-deep:#164c98;
  --navy:#12356e;
  --ink:#1d1d1d;
  --text:#4a4a4a;
  --light:#f3f5f7;
  --footer:#161616;
  --white:#ffffff;
}
*{margin:0;padding:0;box-sizing:border-box}
html,body{width:1200px;height:5279px;overflow:hidden}
body{font-family:"Open Sans",sans-serif;color:var(--text);background:var(--white);position:relative}
h1,h2,h3,h4,.nav a{font-family:"Montserrat",sans-serif}
.abs{position:absolute}
.topbar{top:0;left:140px;width:920px;height:30px;background:var(--green);border-radius:0 0 16px 16px;display:flex;justify-content:center;gap:50px;align-items:center;color:#fff;font-size:13px;z-index:2}
.topbar span{display:flex;align-items:center;gap:7px}
.nav{top:30px;left:0;width:1200px;height:80px;display:flex;justify-content:center;align-items:center;gap:36px}
.nav a{font-size:15px;font-weight:600;color:var(--ink);text-decoration:none;letter-spacing:.3px}
.hero{top:110px;left:0;width:1200px;height:660px;background:linear-gradient(180deg,#2a4f86 0%,#3b6498 55%,#23344a 100%)}
.hero-mark{top:250px;left:570px;width:60px;height:60px;border-radius:50%;background:var(--green)}
.hero-title{top:470px;left:0;width:1200px;text-align:center;color:#fff;font-size:46px;font-weight:600;line-height:1.2}
.arrow{width:34px;height:34px;border-radius:50%;background:rgba(255,255,255,.85);display:flex;align-items:center;justify-content:center}
.title{width:1200px;left:0;text-align:center;color:var(--ink);font-weight:800;font-size:38px;letter-spacing:.5px}
.leaf{width:70px;height:26px}
.welcome-text{top:1010px;left:170px;width:860px;text-align:center;font-size:14px;line-height:2}
.welcome-text p{margin-bottom:18px}
.about-bg{top:1400px;left:0;width:1200px;height:710px;background:linear-gradient(180deg,#fff 0%,#fff 60%,#79b457 78%,#3f7d2e 100%)}
.about-photo{top:1400px;left:0;width:560px;height:710px;background:linear-gradient(180deg,#ffffff 0%,#eef2f4 55%,#6aa84a 75%,#3f7d2e 100%)}
.about-text{top:1510px;left:530px;width:560px;font-size:14px;line-height:1.9;color:var(--text)}
.about-text h2{font-size:38px;font-weight:800;color:var(--ink);margin-bottom:12px}
.doc{top:2330px;width:215px;height:280px;background:linear-gradient(180deg,#eef2f6,#cfd8e2)}
.doc-card{top:2330px;left:376px;width:215px;height:395px;background:var(--green);color:#fff}
.doc-photo{width:215px;height:190px;background:linear-gradient(180deg,#f0f3f6,#c3ced9)}
.doc-card h4{font-size:17px;font-weight:700;margin:14px 0 0 12px;line-height:1.3}
.doc-card p{font-size:12px;margin:6px 12px;line-height:1.5}
.btn-sm{margin:12px;display:inline-block;border:1px solid #fff;font-size:10px;font-weight:700;padding:6px 10px;font-family:"Montserrat",sans-serif}
.services{top:2810px;left:0;width:1200px;height:860px;background:linear-gradient(180deg,var(--blue) 0%,var(--blue-deep) 100%)}
.svc{top:3050px;width:140px;text-align:center;color:#fff;font-size:14px;line-height:1.3}
.svc .ic{width:82px;height:82px;border-radius:50%;border:3px solid #fff;margin:0 auto 10px;display:flex;align-items:center;justify-content:center}
.svc .ic.active{background:var(--green)}
.art-photo{top:3275px;left:150px;width:300px;height:300px;border-radius:50%;border:6px solid #fff;background:linear-gradient(135deg,#d9b862,#b9574a 50%,#4a74b0)}
.art-text{top:3285px;left:490px;width:560px;color:#fff;font-size:13px;line-height:1.9}
.art-text h3{font-size:32px;font-weight:600;margin-bottom:8px}
.rule{width:40px;height:3px;background:var(--green);margin-bottom:18px}
.read-img{top:3905px;width:255px;height:265px}
.read-text{top:3935px;width:240px;font-size:12px;line-height:1.6;background:#fff;padding:16px 18px}
.read-text h4{color:var(--ink);font-size:16px;font-weight:700}
.read-text .by{color:var(--green);font-weight:600;font-size:12px;margin:4px 0 12px}
.read-text .more{color:var(--ink);font-weight:600;margin-top:8px}
.appt{top:4310px;left:0;width:600px;height:510px;background:var(--blue)}
.map{top:4310px;left:600px;width:600px;height:510px;background:linear-gradient(135deg,#eef1f3,#e1e7ea)}
.appt h2{position:absolute;top:45px;left:130px;color:#fff;font-size:30px;font-weight:600}
.field{position:absolute;left:130px;width:385px;height:30px;background:#fff;font-size:11px;color:#888;padding:8px 10px}
.appt .note{position:absolute;top:320px;left:130px;color:#fff;font-size:13px}
.submit{position:absolute;top:365px;left:130px;width:225px;height:38px;background:var(--green);color:#fff;font-family:"Montserrat",sans-serif;font-weight:700;font-size:14px;display:flex;align-items:center;justify-content:center}
.footer{top:4820px;left:0;width:1200px;height:459px;background:var(--footer);color:#ddd}
.footer h3{color:#fff;font-size:22px;font-weight:700;margin-bottom:28px}
.f-contact{position:absolute;top:65px;left:145px;width:300px;font-size:13px;line-height:1.7}
.f-row{display:flex;gap:16px;margin-bottom:22px}
.f-sign{position:absolute;top:65px;left:470px;width:350px;font-size:12px;line-height:1.7}
.email-box{margin-top:30px;width:330px;height:40px;background:#fff;border-radius:20px;display:flex;align-items:center;justify-content:space-between;padding-left:18px;color:#999;font-size:12px}
.email-box b{background:var(--blue);color:#fff;height:40px;border-radius:20px;padding:0 20px;display:flex;align-items:center;font-family:"Montserrat",sans-serif;font-size:12px}
.socials{display:flex;gap:10px;margin-top:22px;margin-left:10px}
.socials i{width:30px;height:30px;border:2px solid #fff;border-radius:50%;display:block}
.f-brand{position:absolute;top:70px;left:830px;width:260px;text-align:center}
.f-brand .mark{width:60px;height:60px;border-radius:50%;background:var(--green);margin:0 auto 14px}
.f-brand div.name{color:#fff;font-family:"Montserrat",sans-serif;font-weight:700;font-size:22px;line-height:1.2}
.copy{position:absolute;top:400px;left:0;width:1200px;text-align:center;font-size:12px;color:#bbb}
</style>
</head>
<body>

<div class="abs topbar">
  <span><svg width="12" height="14" viewBox="0 0 12 14"><path d="M6 0a5 5 0 0 0-5 5c0 4 5 9 5 9s5-5 5-9a5 5 0 0 0-5-5zm0 7a2 2 0 1 1 0-4 2 2 0 0 1 0 4z" fill="#fff"/></svg>4820 Maple Ridge Road, Suite 12, Bedford, OH 44146</span>
  <span style="font-weight:700;font-size:15px"><svg width="13" height="13" viewBox="0 0 24 24"><path d="M6.6 10.8a15 15 0 0 0 6.6 6.6l2.2-2.2a1 1 0 0 1 1-.25 11.4 11.4 0 0 0 3.6.57 1 1 0 0 1 1 1V20a1 1 0 0 1-1 1A17 17 0 0 1 3 4a1 1 0 0 1 1-1h3.5a1 1 0 0 1 1 1c0 1.25.2 2.45.57 3.57a1 1 0 0 1-.25 1z" fill="#fff"/></svg>(440) 555-0172</span>
  <span><svg width="14" height="11" viewBox="0 0 14 11"><rect x=".5" y=".5" width="13" height="10" fill="none" stroke="#fff"/><path d="M.5.5 7 6l6.5-5.5" fill="none" stroke="#fff"/></svg>care@halvorsenserenity.com</span>
</div>

<nav class="abs nav">
  <a>HOME</a><a>ABOUT US</a><a>OUR SERVICES</a><a>GOOD READS</a><a>CONTACT US</a>
</nav>

<section class="abs hero" role="img" aria-label="Photo of a calm lake at dusk under an evening sky"></section>
<div class="abs hero-mark"></div>
<h1 class="abs hero-title">Dr Halvorsen<br>Serenity Center</h1>
<div class="abs arrow" style="top:430px;left:62px"><svg width="12" height="12" viewBox="0 0 12 12"><path d="M8 1 3 6l5 5" fill="none" stroke="#222" stroke-width="2"/></svg></div>
<div class="abs arrow" style="top:430px;left:1086px"><svg width="12" height="12" viewBox="0 0 12 12"><path d="M4 1l5 5-5 5" fill="none" stroke="#222" stroke-width="2"/></svg></div>
<svg class="abs" style="top:650px;left:0" width="1200" height="130" viewBox="0 0 1200 130" preserveAspectRatio="none">
  <path d="M0 80 C300 20 700 0 1200 40 L1200 130 L0 130Z" fill="var(--blue)"/>
  <path d="M0 95 C320 40 720 20 1200 60 L1200 130 L0 130Z" fill="var(--green)"/>
  <path d="M0 112 C340 60 740 42 1200 80 L1200 130 L0 130Z" fill="#fff"/>
</svg>

<h2 class="abs title" style="top:845px">WELCOME TO</h2>
<div class="abs" style="top:900px;left:0;width:1200px;text-align:center;font-family:Montserrat,sans-serif;font-size:24px;font-weight:500;color:var(--ink)">DR HALVORSEN SERENITY CENTER</div>
<svg class="abs leaf" style="top:955px;left:565px" viewBox="0 0 70 26"><path d="M2 22C20 4 50 0 68 4 52 14 30 24 2 22Z" fill="var(--green)"/></svg>
<div class="abs welcome-text">
  <p>Each individual is unique with unique personality and unique needs. Therefore we provide individual treatment customized for you or your child. Multiculturalism also informs our practice. We are a full service mental health practice with the capacity to serve adults, children, teens and their parents.</p>
  <p>We provide high quality evidence based treatment and care including medication management, pharmacogenomic testing, individual psychotherapy, group psychotherapy, art therapy, CBT, DBT and trauma therapy. Our providers are experts in treating variety of illnesses such as depression, anxiety, schizophrenia, ADHD, gender identity concerns and PTSD.</p>
  <p>We are experienced in a variety of methods that help people achieve their psychological goals, and we will discuss with you the best ways to attain the health and wellness that you deserve. We are committed to helping you achieve your optimal level of emotional functioning and fulfill a successful life.</p>
</div>

<div class="abs about-bg"></div>
<div class="abs about-photo" role="img" aria-label="Woman meditating on grass in a white outfit"></div>
<div class="abs about-text">
  <h2>ABOUT US</h2>
  <svg class="leaf" viewBox="0 0 70 26" style="margin-bottom:18px"><path d="M2 22C20 4 50 0 68 4 52 14 30 24 2 22Z" fill="var(--green)"/></svg>
  <p>You will find a number of highly specialized – experienced and caring therapists and psychiatrists in Serenity Center. We provide medication management and psychotherapy (counseling) across the lifespan.</p>
  <p style="color:var(--green);margin:10px 0">◦ children, teens and adults</p>
  <p style="font-size:16px;color:var(--ink)">Other than English, we speak the following languages</p>
  <p style="margin-top:14px;color:var(--ink)">Spanish &nbsp;&nbsp;| &nbsp;&nbsp;German &nbsp;&nbsp;| &nbsp;&nbsp;Farsi &nbsp;&nbsp;| &nbsp;&nbsp;Hebrew</p>
</div>

<h2 class="abs title" style="top:2180px">OUR DOCTORS</h2>
<svg class="abs leaf" style="top:2245px;left:565px" viewBox="0 0 70 26"><path d="M2 22C20 4 50 0 68 4 52 14 30 24 2 22Z" fill="var(--green)"/></svg>
<div class="abs doc" style="left:143px" role="img" aria-label="Portrait of a female doctor"></div>
<div class="abs doc-card">
  <div class="doc-photo" role="img" aria-label="Portrait of a male doctor"></div>
  <h4>MARELLA<br>Psychotherapy</h4>
  <p>Sed ut perspiciatis unde omnis iste natus error sit voluptatem</p>
  <span class="btn-sm">MAKE AN APPOINTMENT</span>
</div>
<div class="abs doc" style="left:609px" role="img" aria-label="Portrait of a female doctor"></div>
<div class="abs doc" style="left:842px" role="img" aria-label="Portrait of a senior male doctor"></div>

<section class="abs services"></section>
<h2 class="abs title" style="top:2895px;color:#fff">OUR SERVICES</h2>
<svg class="abs leaf" style="top:2955px;left:565px" viewBox="0 0 70 26"><path d="M2 22C20 4 50 0 68 4 52 14 30 24 2 22Z" fill="#fff"/></svg>
<div class="abs svc" style="left:135px"><div class="ic"><svg width="34" height="34" viewBox="0 0 34 34"><rect x="9" y="4" width="16" height="26" rx="3" fill="none" stroke="#fff" stroke-width="2"/><path d="M17 12v10M12 17h10" stroke="#fff" stroke-width="2"/></svg></div>Medication management</div>
<div class="abs svc" style="left:325px;width:150px"><div class="ic"><svg width="36" height="30" viewBox="0 0 36 30"><circle cx="11" cy="9" r="5" fill="none" stroke="#fff" stroke-width="2"/><circle cx="25" cy="9" r="5" fill="none" stroke="#fff" stroke-width="2"/><path d="M2 28c0-7 18-7 18 0M16 28c0-7 18-7 18 0" fill="none" stroke="#fff" stroke-width="2"/></svg></div>Psychotherapy individual, group, couples</div>
<div class="abs svc" style="left:525px"><div class="ic active"><svg width="34" height="34" viewBox="0 0 34 34"><circle cx="17" cy="17" r="11" fill="none" stroke="#fff" stroke-width="2"/><circle cx="13" cy="13" r="2" fill="#fff"/><circle cx="21" cy="13" r="2" fill="#fff"/><circle cx="13" cy="21" r="2" fill="#fff"/></svg></div>Art Therapy</div>
<div class="abs svc" style="left:720px"><div class="ic"><svg width="34" height="34" viewBox="0 0 34 34"><path d="M6 16h6v14H6zM12 28h12l4-10h-9l2-8-3-2-6 10" fill="none" stroke="#fff" stroke-width="2"/></svg></div>Treatment Approach</div>
<div class="abs svc" style="left:915px"><div class="ic"><svg width="34" height="34" viewBox="0 0 34 34"><rect x="6" y="6" width="22" height="22" fill="none" stroke="#fff" stroke-width="2"/><path d="M11 14h12M11 20h12" stroke="#fff" stroke-width="2"/></svg></div>Treatment Areas</div>
<div class="abs art-photo" role="img" aria-label="Colorful painting of a woman with flowing hair"></div>
<div class="abs art-text">
  <h3>Art Therapy</h3>
  <div class="rule"></div>
  <p>Sed ut perspiciatis unde omnis iste natus error sit voluptatem accusantium doloremque laudantium, totam rem aperiam, eaque ipsa quae ab illo inventore veritatis et quasi architecto beatae vitae dicta sunt explicabo. Nemo enim ipsam voluptatem quia voluptas sit aspernatur aut odit aut fugit, sed quia consequuntur magni dolores eos qui ratione voluptatem sequi nesciunt.</p>
</div>
<svg class="abs" style="top:3410px;left:70px" width="16" height="28" viewBox="0 0 16 28"><path d="M14 2 3 14l11 12" fill="none" stroke="#fff" stroke-width="2.5"/></svg>
<svg class="abs" style="top:3410px;left:1100px" width="16" height="28" viewBox="0 0 16 28"><path d="M2 2l11 12L2 26" fill="none" stroke="#fff" stroke-width="2.5"/></svg>

<h2 class="abs title" style="top:3755px">GOOD READS</h2>
<svg class="abs leaf" style="top:3815px;left:565px" viewBox="0 0 70 26"><path d="M2 22C20 4 50 0 68 4 52 14 30 24 2 22Z" fill="var(--green)"/></svg>
<div class="abs read-img" style="left:143px;background:linear-gradient(180deg,#1a2a5e,#3d6fb5)" role="img" aria-label="Open book glowing under a starry sky"></div>
<div class="abs read-text" style="left:335px">
  <h4>NEMO ENIM IPSAM</h4><div class="by">Nadia Cole</div>
  <p>Sed ut perspiciatis unde omnis iste natus error sit voluptatem accusantium doloremque laudantium</p>
  <p class="more">Read More ›</p>
</div>
<div class="abs read-img" style="left:622px;background:linear-gradient(180deg,#6a3a12,#c98a34)" role="img" aria-label="Open book with golden light rising from its pages"></div>
<div class="abs read-text" style="left:815px">
  <h4>NEMO ENIM IPSAM</h4><div class="by">Nadia Cole</div>
  <p>Sed ut perspiciatis unde omnis iste natus error sit voluptatem accusantium doloremque laudantium</p>
  <p class="more">Read More ›</p>
</div>

<section class="abs appt">
  <h2>Appointment Request</h2>
  <div class="field" style="top:115px">First Name</div>
  <div class="field" style="top:160px">Last Name</div>
  <div class="field" style="top:205px">Email Address</div>
  <div class="field" style="top:250px">Phone Number</div>
  <p class="note">Please contact me for an appointment</p>
  <div class="submit">SUBMIT</div>
</section>
<div class="abs map" role="img" aria-label="Street map showing the clinic location"></div>
<svg class="abs" style="top:4760px;left:0" width="1200" height="80" viewBox="0 0 1200 80" preserveAspectRatio="none">
  <path d="M0 40 C400 0 800 10 1200 20 L1200 80 L0 80Z" fill="var(--blue)"/>
  <path d="M0 55 C400 18 800 28 1200 38 L1200 80 L0 80Z" fill="var(--green)"/>
  <path d="M0 68 C400 34 800 44 1200 54 L1200 80 L0 80Z" fill="var(--footer)"/>
</svg>

<footer class="abs footer">
  <div class="f-contact">
    <h3>CONTACT US</h3>
    <div class="f-row"><svg width="14" height="18" viewBox="0 0 12 14"><path d="M6 0a5 5 0 0 0-5 5c0 4 5 9 5 9s5-5 5-9a5 5 0 0 0-5-5zm0 7a2 2 0 1 1 0-4 2 2 0 0 1 0 4z" fill="#fff"/></svg><span>Dr Halvorsen Serenity Center<br>4820 Maple Ridge Road, Suite 12, Bedford, OH 44146</span></div>
    <div class="f-row"><svg width="14" height="14" viewBox="0 0 24 24"><path d="M6.6 10.8a15 15 0 0 0 6.6 6.6l2.2-2.2a1 1 0 0 1 1-.25 11.4 11.4 0 0 0 3.6.57 1 1 0 0 1 1 1V20a1 1 0 0 1-1 1A17 17 0 0 1 3 4a1 1 0 0 1 1-1h3.5a1 1 0 0 1 1 1c0 1.25.2 2.45.57 3.57a1 1 0 0 1-.25 1z" fill="#fff"/></svg><span>Phone:<br>(440) 555-0172</span></div>
    <div class="f-row"><svg width="14" height="11" viewBox="0 0 14 11"><rect x=".5" y=".5" width="13" height="10" fill="none" stroke="#fff"/><path d="M.5.5 7 6l6.5-5.5" fill="none" stroke="#fff"/></svg><span>Email:<br>care@halvorsenserenity.com</span></div>
  </div>
  <div class="f-sign">
    <h3>SIGN UP TO RECEIVE EMAIL</h3>
    <p>Receive our latest news, helpful articles and upcoming events in your inbox, delivered monthly.</p>
    <div class="email-box">Enter Email <b>SUBSCRIBE</b></div>
    <div class="socials"><i></i><i></i><i></i></div>
  </div>
  <div class="f-brand">
    <div class="mark"></div>
    <div class="name">Dr Halvorsen<br>Serenity Center</div>
  </div>
  <p class="copy">2019 © Copyrights Dr Halvorsen Serenity Center All Rights Reserved</p>
</footer>

</body>
</html>
```